Website Banner Redesign for Kelvra Cargo Depot

Business Name:
KELVRA CARGO DEPOT

About Us:
- We’re a proudly Australian company that designs and builds tough, reliable toolboxes for Utes, Trucks, and Campervans. Our products are made to handle harsh conditions and are trusted by tradies, off-roaders, and professional fleets across the country.

Project Goal:
- We want to refresh our homepage and category banners with bold, modern designs that better showcase our products and value proposition.

Why We’re Updating:
Our current banners show the products well, but we want to improve:
Visual impact and hierarchy
- Readability of text (especially on mobile)
- Clearer calls-to-action (CTAs)
- Brand messaging around “Built Tough”, “Aussie Made”, and “Custom Fit-Outs”

Target Audience:
- Tradespeople
- 4x4 & off-road enthusiasts
- Caravan & camping community
- Ute/Truck/Caravan dealerships
- Fleet and commercial buyers

Design Style We Want:
- Bold, confident, rugged
- Clean layout with clear focal points
- Strong product imagery (we’ll supply photos)
- Use of brand colors: Black, White, Red, Grey
- Professional, not too busy or cluttered

Banner Uses:
- Homepage hero banner
- Category landing pages

UTE TOOLBOXES - https://www.kelvracargo.com.au/aluminium-toolboxes/
Truck Boxes - https://www.kelvracargo.com.au/truck-toolboxes/
Canopies - https://www.kelvracargo.com.au/canopy/
Dog Boxes - https://www.kelvracargo.com.au/dog-boxes/
CAMPER BOXES - https://www.kelvracargo.com.au/camper-toolboxes/
Accessories - https://www.kelvracargo.com.au/accessories/

- Can be reused for desktop and mobile

Inspiration Style:
Think: 4x4 accessory brands, tough tradie gear, or clean eCommerce landing banners from premium auto suppliers.

Target Market(s)

All in Brief Above

Industry/Entity Type

Retail

Requirements
Must have
• A banner using our products only. A banner for each category, and 2 alternate banners for the home page.
Nice to have
• I have added some designs which i like..... Please take a look and take inspiration from them.

```html
<!DOCTYPE html>
<html lang="en">
<head>
<meta charset="utf-8">
<title>Kelvra Cargo Depot – Tool Box Accessories</title>
<link rel="stylesheet" href="https://fonts.googleapis.com/css2?family=Anton&display=swap">
<style>
  :root {
    --bg-dark: #1c2932;
    --bg-mid: #33454f;
    --bg-glow: #5a6d77;
    --text-white: #ffffff;
    --accent-yellow: #ffcc00;
    --cta-red: #a91d4c;
  }
  * { margin: 0; padding: 0; box-sizing: border-box; }
  html, body { width: 900px; height: 1200px; overflow: hidden; background: var(--bg-dark); }
  .banner {
    position: relative;
    width: 900px;
    height: 1200px;
    overflow: hidden;
    font-family: "Anton", "Impact", sans-serif;
    background:
      radial-gradient(ellipse 420px 260px at 450px 640px, var(--bg-glow) 0%, rgba(90,109,119,0) 100%),
      radial-gradient(ellipse 600px 380px at 330px 170px, #42555f 0%, rgba(66,85,95,0) 100%),
      linear-gradient(160deg, var(--bg-mid) 0%, var(--bg-dark) 60%, #141d23 100%);
  }
  .headline {
    position: absolute;
    left: 88px;
    top: 62px;
    color: var(--text-white);
    font-size: 152px;
    line-height: 144px;
    letter-spacing: 1px;
    text-transform: uppercase;
    font-weight: 400;
  }
  .product-photos {
    position: absolute;
    left: 100px;
    top: 520px;
    width: 700px;
    height: 260px;
    display: flex;
    justify-content: space-between;
  }
  .product-photos .latch {
    width: 330px;
    height: 260px;
    border-radius: 46% 46% 40% 40%;
  }
  .latch--black { background: radial-gradient(circle at 55% 45%, #8a8f93 0%, #2a2c2e 45%, #121314 100%); }
  .latch--chrome { background: radial-gradient(circle at 50% 45%, #ffffff 0%, #c9ced2 45%, #7f878c 100%); width: 260px !important; }
  .subhead {
    position: absolute;
    left: 96px;
    top: 820px;
    color: var(--accent-yellow);
    font-size: 74px;
    line-height: 80px;
    text-transform: uppercase;
  }
  .cta {
    position: absolute;
    left: 90px;
    top: 1015px;
    width: 642px;
    height: 124px;
    border-radius: 18px;
    background: var(--cta-red);
    color: var(--text-white);
    font-size: 70px;
    line-height: 124px;
    text-align: center;
    text-decoration: none;
    text-transform: uppercase;
  }
</style>
</head>
<body>
  <main class="banner">
    <h1 class="headline">Essential<br>Tool&nbsp;&nbsp;Box<br>Accessories</h1>
    <div class="product-photos">
      <div class="latch latch--black" role="img" aria-label="Black recessed tool box latch with chrome handle and wiring"></div>
      <div class="latch latch--chrome" role="img" aria-label="Chrome stainless tool box latch with lock barrel"></div>
    </div>
    <p class="subhead">Enhance functionality<br>with quality add-ons</p>
    <a class="cta" href="https://www.kelvracargo.com.au/accessories/">Shop Accessories</a>
  </main>
</body>
</html>
```